Brightmoor - a website to encourage people to spend time in nature

I have a squarespace site with some content on it but the squarespace template doesn't completely suit my needs, I keep fiddling with the template but actually I need some professional help to get it looking the way I want and with the right 'mood'.
The website is for "Brightmoor" - it will be a blog where I write about the importance of nature for good health. I also want to use the website to market services such as outdoor coaching, retreats and walking workshops.
This has been in my head for a LONG time and I currently only use instagram for micro-blogs but it's time for me to get this moving. I've previously engaged other designers on branding for it but they just didn't get it quite the way that I wanted it and I wasn't completely happy with the results. It's been a process for me as to what I want but in the meantime I just didn't come back to the design aspect of it now. I'm looking for a designer who understands the purpose of the website, the ethos and can help me realise this into a design that's clean, clear and simple.

Please note that I have a domain (brightmoor.org) and a lot of content drafted on squarespace already. I have published it with password protection - password is brightmoor2020 - it still has some of the original template on it, but does have some content. Don't take it as anything to follow in particular, i am looking for fresh eyes and fresh ideas.

Target Market(s)

There are three main groups that I want to target - people who are suffering from stress and anxiety, people who treat them and parents who want to get their kids outside (thereby preventing stress and anxiety)

Contact Information for Business Card

Joan Petrie
Brightmoor
Telephone +44 7700 900417
brightmoor@mailvane.com

Logo Text

Brightmoor - if that. I have an idea that the logo should have a leaf on it somewhere, or maybe just be a leaf.

Coding

Coded - Design and coding required

Number of Pages Required

5+ page

Font styles to use
Serif
Sans Serif

Colors
add136
33b8a4
34a6d7
3377b5

Requirements
Must have
• Space for lots of images. The ability for me to edit the pages if I need to. Be user friendly. Look beautiful.
• For an idea of the images I use and the content I'm interested in writing about have a look at @brightmoor on instagram.
• That pop up about cookies so I am complying with data laws.
Should not have
• Must not be too 'busy' I'd like to avoid too much movement.

```html
<!DOCTYPE html>
<html lang="en">
<head>
<meta charset="utf-8">
<title>Brightmoor</title>
<link rel="stylesheet" href="https://fonts.googleapis.com/css2?family=Lato:wght@300;400;700&display=swap">
<style>
:root{
  --teal:#33b8a4;
  --ocean:#3377b5;
  --sky:#34a6d7;
  --ink:#333;
  --white:#fff;
  --line:#c9c9c9;
}
*{box-sizing:border-box;margin:0;padding:0}
html,body{width:1200px;height:4090px;overflow:hidden}
body{font-family:'Lato',sans-serif;color:var(--ink);background:var(--white);position:relative}
section,header,footer{position:relative;width:1200px}
.abs{position:absolute}
.btn{position:absolute;width:165px;height:54px;background:var(--teal);color:var(--white);font-size:18px;display:flex;align-items:center;justify-content:center;border:0;font-family:inherit}

/* hero */
.hero{height:544px;background:linear-gradient(180deg,#2d3a26 0%,#4a6a35 40%,#5f8a3c 70%,#3f5a2c 100%);color:var(--white)}
.hero .photo{position:absolute;inset:0}
.brand{left:75px;top:52px;font-size:40px;font-weight:300;letter-spacing:8px;text-transform:uppercase;line-height:1}
.nav{left:0;top:64px;width:1200px;height:30px}
.nav a{position:absolute;color:var(--white);text-decoration:none;font-size:15px;text-transform:uppercase;letter-spacing:.5px}
.nav a.current{border-bottom:3px solid var(--sky);padding:0 14px 6px;margin-left:-14px}
.hero h1{left:0;width:1200px;top:198px;text-align:center;font-size:70px;font-weight:400}
.hero .tagline{left:0;width:1200px;top:285px;text-align:center;font-size:30px;font-weight:300;line-height:38px}

/* intro */
.intro{height:431px}
.intro h2{left:75px;top:74px;width:520px;font-size:40px;font-weight:400;line-height:59px}
.intro p{left:614px;top:80px;width:520px;font-size:16.5px;line-height:27.6px}
.intro .btn{left:75px;top:286px}

/* features */
.features{height:1414px;background:var(--ocean);color:var(--white)}
.features .photo{position:absolute;width:512px;height:370px}
.features h3{font-size:42px;font-weight:400;line-height:44px;width:520px}
.features p{font-size:16.5px;line-height:27.6px;width:520px}

/* planet */
.planet{height:1046px}
.planet h2{left:75px;top:106px;font-size:42px;font-weight:400;line-height:49px}
.planet p{left:75px;top:200px;font-size:19px;line-height:31px}
.planet .btn{left:75px;top:301px}
.planet .photo{left:75px;top:452px;width:1052px;height:473px;background:linear-gradient(180deg,#2c3b22 0%,#5c8a32 50%,#7aa848 75%,#4d6a2e 100%)}

/* contact */
.contact{height:488px}
.contact h2{left:75px;top:36px;font-size:44px;font-weight:400}
.contact .lead{left:73px;top:100px;font-size:19px}
.contact dl{left:75px;top:143px;font-size:16px;line-height:24px}
.contact dt{font-weight:700}
.contact dd{margin-bottom:30px}
.field{position:absolute;border:1px solid var(--line);background:var(--white);font-size:15px;padding:14px 15px;color:#444}
.contact .btn{left:524px;top:380px}

/* footer */
.site-footer{height:287px;background:var(--sky);color:var(--white)}
.site-footer .brand{left:75px;top:58px;font-size:34px;letter-spacing:7px}
.site-footer address{left:75px;top:113px;font-style:normal;font-size:15px;line-height:27px}
.site-footer h4{font-size:25px;font-weight:400;margin-bottom:6px}
.site-footer ul{list-style:none;font-size:14px;line-height:27px}
</style>
</head>
<body>

<header class="hero">
  <div class="photo" role="img" aria-label="Sunlit woodland path between tall trees and green undergrowth"></div>
  <div class="abs brand">Brightmoor</div>
  <nav class="abs nav">
    <a class="current" style="left:660px">Home</a>
    <a style="left:751px">About</a>
    <a style="left:848px">Blog</a>
    <a style="left:933px">Gallery</a>
    <a style="left:1044px">Contact</a>
  </nav>
  <h1 class="abs">Brightmoor</h1>
  <p class="abs tagline">Our mission is to get people of all ages outdoors<br>as a means to feel better.</p>
</header>

<section class="intro">
  <h2 class="abs">Brightmoor — the practice of feeling better by spending time in nature.</h2>
  <p class="abs">Brightmoor Walking is an initiative aimed at getting people back into nature in the most gentlest of ways - by taking a walk with friends in the great outdoors. The concept is simple - schedule a walk outside, once a week with two or three other people.<br>That's it. Sometimes the best things are the simplest and here's why this works.<br>Walking - for most people it's the most accessible form of exercise. You don't need fancy equipment, there are few barriers to entry, it's low impact, it can slot into your day without a huge amount of effort.</p>
  <a class="btn" style="left:75px;top:286px">Read More</a>
</section>

<section class="features">
  <div class="photo" style="left:75px;top:74px;background:linear-gradient(180deg,#cfd9e4 0%,#8ea3b8 40%,#4a4a44 60%,#2a2825 100%)" role="img" aria-label="Adult and child walking over a rocky shoreline under a cloudy sky"></div>
  <h3 class="abs" style="left:614px;top:140px">Anxiety and Stress</h3>
  <p class="abs" style="left:614px;top:188px">Suspendisse et porta mi. In arcu magna, semper a nisi ac, maximus semper felis. In sagittis justo sem, sed fringilla velit elementum sed. Praesent fringilla maximus odio, fringilla finibus est malesuada in. Vestibulum fermentum ultricies venenatis.</p>
  <a class="btn" style="left:614px;top:331px">Read More</a>

  <h3 class="abs" style="left:75px;top:578px">Outdoor Coaching</h3>
  <p class="abs" style="left:75px;top:626px">Suspendisse et porta mi. In arcu magna, semper a nisi ac, maximus semper felis. In sagittis justo sem, sed fringilla velit elementum sed. Praesent fringilla maximus odio, fringilla finibus est malesuada in. Vestibulum fermentum ultricies venenatis.</p>
  <a class="btn" style="left:75px;top:769px">Read More</a>
  <div class="photo" style="left:614px;top:512px;background:linear-gradient(180deg,#4c5048 0%,#3a3e38 50%,#2c2f2a 100%)" role="img" aria-label="Swimmer in dark open water"></div>

  <div class="photo" style="left:75px;top:956px;background:linear-gradient(180deg,#3a4034 0%,#4e5244 50%,#3b3a34 100%)" role="img" aria-label="Family walking together along a woodland path"></div>
  <h3 class="abs" style="left:614px;top:1000px">Retreats &amp; Walking<br>Workshops</h3>
  <p class="abs" style="left:614px;top:1091px">Suspendisse et porta mi. In arcu magna, semper a nisi ac, maximus semper felis. In sagittis justo sem, sed fringilla velit elementum sed. Praesent fringilla maximus odio, fringilla finibus est malesuada in. Vestibulum fermentum ultricies venenatis.</p>
  <a class="btn" style="left:614px;top:1242px">Read More</a>
</section>

<section class="planet">
  <h2 class="abs">Why being outside is good<br>for the planet</h2>
  <p class="abs">The focus of Brightmoor is on people. Making people feel better through time spent in nature.<br>Making the world a better place because the people in it are happier.</p>
  <a class="btn">Read More</a>
  <div class="photo abs" role="img" aria-label="Sunlit grassy path through a green forest"></div>
</section>

<section class="contact">
  <h2 class="abs">Contact</h2>
  <p class="abs lead">Feel free to contact us with any questions.</p>
  <dl class="abs">
    <dt>Email:</dt><dd>hello@brightmoor.org</dd>
    <dt>Phone:</dt><dd>1-800-555-0142</dd>
  </dl>
  <div class="field" style="left:524px;top:37px;width:295px;height:47px">Name</div>
  <div class="field" style="left:833px;top:37px;width:295px;height:47px">Phone</div>
  <div class="field" style="left:524px;top:98px;width:604px;height:48px">Email Address</div>
  <div class="field" style="left:524px;top:162px;width:604px;height:112px">Message</div>
  <button class="btn">Submit</button>
</section>

<footer class="site-footer">
  <div class="abs brand">Brightmoor</div>
  <address class="abs">48 Fern Lane<br>Hollowbrook, HB 20417</address>
  <div class="abs" style="left:614px;top:52px">
    <h4>About</h4>
    <ul><li>Nam in nulla tincidunt</li><li>Venenatis magna</li></ul>
  </div>
  <div class="abs" style="left:884px;top:52px">
    <h4>Services</h4>
    <ul><li>Nam in nulla tincidunt</li><li>Venenatis magna</li><li>Vivamus a metus</li><li>Vel augue</li></ul>
  </div>
</footer>

</body>
</html>
```